OBK Farcoast Logistics Limited

We need the buissnes card to be very exclusive. As we are all young in our company. We need this to be the gate to make our clients feel deep interest for us.

We are focused in as International Trade advisors, and our products go from Oil Tanker Ships to Rubber balls for dogs.

Our Slogan is Bringing World Home.
And our main marketing will be through Internet.

We were stablished in 2009 In Mexico and we also have offices in Hong Kong.
We have representatives in China and Europe.

Target Market(s)

Is every company or Individual that wants to develop an International Project or product development or Logistic service of Goods and people.
Some of our current projects are Ship Brokerage, Mine Brokerage, Real State and Product Pormotional development.

Industry/Entity Type

It Company

Requirements
Must have
• Our Logo and slogan, and make the card accoriding to the logo.
Nice to have
• Our Colors

```html
<!DOCTYPE html>
<html lang="en">
<head>
<meta charset="utf-8">
<title>Business Card – Front and Back</title>
<link href="https://fonts.googleapis.com/css2?family=Open+Sans:wght@400;600;700&display=swap" rel="stylesheet">
<style>
  :root {
    --backdrop: #e6e6ea;
    --card-black: #050505;
    --brand-green: #8dc63f;
    --brand-blue: #1f7fc4;
    --ink-white: #ffffff;
    --ink-dark: #141414;
    --divider: #8a8a8a;
  }
  * { box-sizing: border-box; margin: 0; padding: 0; }
  html, body { width: 1200px; height: 987px; overflow: hidden; }
  body {
    background: var(--backdrop);
    font-family: "Open Sans", Arial, sans-serif;
    position: relative;
  }
  .card {
    position: absolute;
    width: 720px;
    height: 411px;
    border-radius: 36px;
    background: var(--card-black);
    overflow: hidden;
    box-shadow: 0 10px 28px rgba(0,0,0,0.18);
  }
  .card--front { left: 240px; top: 40px; }
  .card--back  { left: 240px; top: 536px; }
  .card__swoosh { position: absolute; inset: 0; }

  .brand-mark {
    position: absolute;
    display: flex;
    align-items: center;
    gap: 14px;
    color: var(--brand-green);
    font-weight: 700;
    letter-spacing: 4px;
    line-height: 1;
  }
  .brand-mark__dot {
    border-radius: 50%;
    background: var(--brand-blue);
  }
  .card--front .brand-mark { left: 90px; top: 136px; font-size: 76px; }
  .card--front .brand-mark__dot { width: 40px; height: 40px; }

  .divider {
    position: absolute;
    left: 345px; top: 70px;
    width: 1px; height: 210px;
    background: var(--divider);
  }
  .contact {
    position: absolute;
    left: 368px; top: 66px;
    color: var(--ink-white);
    font-size: 18px;
    line-height: 1.35;
  }
  .contact__name { color: var(--brand-green); font-weight: 700; font-size: 24px; }
  .contact__title { margin-bottom: 12px; }
  .contact__row { display: flex; align-items: center; gap: 8px; }
  .contact__row svg { width: 15px; height: 15px; fill: var(--brand-green); flex: none; }
  .contact__address { margin-top: 8px; }

  .slogan-front {
    position: absolute;
    left: 430px; bottom: 22px;
    color: var(--ink-dark);
    font-size: 24px;
  }

  .card--back .brand-lockup {
    position: absolute;
    left: 0; right: 0; top: 120px;
    display: flex; flex-direction: column; align-items: center;
  }
  .card--back .brand-mark { position: static; font-size: 84px; }
  .card--back .brand-mark__dot { width: 44px; height: 44px; }
  .brand-slogan { color: var(--brand-blue); font-size: 15px; margin-top: 10px; }
  .website {
    position: absolute;
    left: 0; right: 0; bottom: 80px;
    text-align: center;
    color: var(--ink-white);
    font-size: 22px;
    letter-spacing: 6px;
  }
</style>
</head>
<body>

<section class="card card--front" aria-label="Business card front">
  <svg class="card__swoosh" viewBox="0 0 720 411" aria-hidden="true">
    <path d="M0,120 C20,250 150,330 330,320 C470,312 600,330 720,395 L720,411 L0,411 Z" fill="var(--brand-green)"/>
    <path d="M0,95 C6,160 30,215 70,255" fill="none" stroke="var(--brand-blue)" stroke-width="7"/>
    <path d="M470,300 C570,298 660,330 720,372" fill="none" stroke="var(--brand-blue)" stroke-width="8"/>
  </svg>

  <div class="brand-mark"><span class="brand-mark__dot"></span>OBK</div>

  <div class="divider"></div>

  <div class="contact">
    <div class="contact__name">Your Name</div>
    <div class="contact__title">Title</div>
    <div class="contact__row">
      <svg viewBox="0 0 16 16"><path d="M3 1l3 3-1.5 2a9 9 0 0 0 5.5 5.5L12 10l3 3-2 2C7 15 1 9 1 3z"/></svg>123-456-0789
    </div>
    <div class="contact__row">
      <svg viewBox="0 0 16 16"><rect x="4" y="1" width="8" height="14" rx="1.5"/></svg>123-456-0789
    </div>
    <div class="contact__row">
      <svg viewBox="0 0 16 16"><path d="M1 3h14v10H1z"/></svg>info@obktradeline.com
    </div>
    <div class="contact__row">
      <svg viewBox="0 0 16 16"><circle cx="8" cy="8" r="7"/></svg>www.obktradeline.com
    </div>
    <div class="contact__address">Street Name, City Name<br>State Zip Code</div>
  </div>

  <div class="slogan-front">Bringing World Home</div>
</section>

<section class="card card--back" aria-label="Business card back">
  <div class="brand-lockup">
    <div class="brand-mark"><span class="brand-mark__dot"></span>OBK</div>
    <div class="brand-slogan">Bringing World Home</div>
  </div>
  <div class="website">www.obktradeline.com</div>
</section>

</body>
</html>
```